Meridale Bed Company Needs Business Card

Looking for a very nice looking business card. Creative but not extravagant. We sell beds and pillows across the U.S. and need something professional but catchy. I have attached the logo.

Name : Devin Holt
Title : President
Phone : (800) 471-2960
Email: sleep@quilmora.com
Website: www.quilmora.com

Can be single-sided or double-sided
horizontal or vertical

Can use Blues/Greys

Target Market(s)

Mass Market

Industry/Entity Type

Retail

Contact Information for Business Card

Name : Devin Holt
Title : President
Phone : (800) 471-2960
Email: sleep@quilmora.com
Website: www.quilmora.com

Requirements
Must have
• Clean, Modern, Smooth
• Can use Blues/Greys
• On the other side without the information - have something simple like www.quilmora.com or our logo
Nice to have
• Surprise me
Should not have
• Nothing crazy, nothing cluttered

```html
<!DOCTYPE html>
<html lang="en">
<head>
<meta charset="utf-8">
<title>Quilmora Business Card</title>
<link href="https://fonts.googleapis.com/css2?family=Lato:wght@300;400;700;900&display=swap" rel="stylesheet">
<style>
  :root {
    --backdrop: #2b2b2d;
    --card-white: #f4f4f4;
    --brand-blue: #2a97c9;
    --brand-blue-deep: #1f86b8;
    --text-light: #ffffff;
    --text-soft: #e8f4fb;
  }
  * { margin: 0; padding: 0; box-sizing: border-box; }
  html, body {
    width: 1200px;
    height: 873px;
    overflow: hidden;
    background: var(--backdrop);
    font-family: "Lato", sans-serif;
  }
  .card {
    position: absolute;
    left: 180px;
    top: 196px;
    width: 840px;
    height: 480px;
    border-radius: 26px;
    overflow: hidden;
    background: var(--card-white);
    box-shadow: 0 18px 40px rgba(0,0,0,0.45);
  }
  .brand-panel {
    position: absolute;
    left: 0;
    top: 0;
    width: 336px;
    height: 100%;
    background: linear-gradient(160deg, #fbfbfb, #ececec);
  }
  .brand-name {
    position: absolute;
    left: 0;
    width: 100%;
    top: 222px;
    text-align: center;
    font-weight: 300;
    font-size: 70px;
    letter-spacing: 1px;
    color: var(--brand-blue);
  }
  .divider {
    position: absolute;
    left: 336px;
    top: 0;
    width: 21px;
    height: 100%;
    background: linear-gradient(90deg,
      var(--brand-blue) 0 6px,
      #ffffff 6px 11px,
      var(--brand-blue) 11px 16px,
      #ffffff 16px 21px);
  }
  .info-panel {
    position: absolute;
    left: 357px;
    top: 0;
    right: 0;
    height: 100%;
    background: linear-gradient(160deg, var(--brand-blue), var(--brand-blue-deep));
    color: var(--text-light);
    padding: 112px 0 0 70px;
  }
  .person-name {
    font-weight: 900;
    font-size: 30px;
    line-height: 1;
  }
  .person-title {
    font-weight: 400;
    font-size: 20px;
    margin: 6px 0 0 12px;
    color: var(--text-soft);
  }
  .contact-list {
    list-style: none;
    margin: 22px 0 0 28px;
  }
  .contact-item {
    display: flex;
    align-items: center;
    gap: 12px;
    font-size: 23px;
    font-weight: 400;
    margin-bottom: 12px;
  }
  .contact-icon { width: 24px; height: 20px; flex: none; }
  .website {
    margin: 22px 0 0 48px;
    font-weight: 900;
    font-size: 22px;
    letter-spacing: 5px;
  }
</style>
</head>
<body>
  <div class="card">
    <div class="brand-panel">
      <div class="brand-name">quilmora</div>
    </div>
    <div class="divider"></div>
    <div class="info-panel">
      <div class="person-name">Devin Holt</div>
      <div class="person-title">President</div>
      <ul class="contact-list">
        <li class="contact-item">
          <svg class="contact-icon" viewBox="0 0 24 20" aria-hidden="true">
            <path d="M2 7 Q12 1 22 7 L20 10 L16 8 L16 6 Q12 4.5 8 6 L8 8 L4 10 Z" fill="#fff"/>
            <rect x="6" y="10" width="12" height="8" rx="1.5" fill="#fff"/>
          </svg>
          <span>(800) 471-2960</span>
        </li>
        <li class="contact-item">
          <svg class="contact-icon" viewBox="0 0 24 20" aria-hidden="true">
            <rect x="2" y="3" width="20" height="14" fill="#fff"/>
            <path d="M2 3 L12 11 L22 3 M2 17 L9 9 M22 17 L15 9" stroke="#2a97c9" stroke-width="1.4" fill="none"/>
          </svg>
          <span>sleep@quilmora.com</span>
        </li>
      </ul>
      <div class="website">www.quilmora.com</div>
    </div>
  </div>
</body>
</html>
```